Professional Services - letterhead / business cards

The company (velmora partners) will provide services to Investment Funds and large investors in Spain. I have recently chosen a logo that I am attaching.

I would like a simple stationary design that i could use as letter head, business cards and "with compliments" cards.

I am not quite sure which color I will mostly use for the logo, in the email signature I will probably lean towards the white background and grey letters. I am attaching my favourite options.

Target Market(s)

Large Multinationals, Investment funds and Law firms

Industry/Entity Type

Business

Requirements
Must have
• my details are:
Luis R. Abadal
Velmora Partners S.L.
Casa de Torrelumbre
Calle de Vientoalto 27
28014 Madrid
T: +34 (91) 387-2265
M: +34 (646) 819-054
e-mail: labadal@velmorapartners.com

```html
<!DOCTYPE html>
<html lang="en">
<head>
<meta charset="utf-8">
<title>Velmora Partners – Business Cards</title>
<link rel="stylesheet" href="https://fonts.googleapis.com/css2?family=Arimo:wght@400;700&display=swap">
<style>
  :root {
    --navy: #25266a;
    --grey: #a7a9ac;
    --white: #ffffff;
    --ink-dark: #3a3a3c;
    --backdrop: #e9e6e1;
  }
  * { margin: 0; padding: 0; box-sizing: border-box; }
  html, body { width: 1200px; height: 711px; overflow: hidden; }
  body {
    background: var(--backdrop);
    position: relative;
    font-family: "Arimo", sans-serif;
  }
  .card {
    position: absolute;
    top: 205px;
    width: 520px;
    height: 300px;
    overflow: hidden;
    box-shadow: 0 6px 18px rgba(0,0,0,0.18);
  }
  .card--front { left: 50px; background: var(--white); }
  .card--back { left: 630px; background: var(--navy); }

  /* brand name placeholder */
  .brand {
    position: absolute;
    left: 0; right: 0;
    display: flex;
    justify-content: center;
    align-items: center;
    gap: 14px;
    font-size: 32px;
    font-weight: 400;
    line-height: 1;
  }
  .brand__mark { width: 16px; height: 16px; }
  .front__brand { top: 62px; color: var(--navy); }
  .front__brand .brand__mark { background: var(--navy); }
  .back__brand { top: 112px; color: var(--white); }
  .back__brand .brand__mark { background: var(--white); }

  /* front */
  .front__band {
    position: absolute;
    left: 0; right: 0; top: 150px;
    height: 50px;
    background: var(--grey);
  }
  .front__rule {
    position: absolute;
    left: 0; right: 0; top: 200px;
    height: 4px;
    background: var(--white);
  }
  .front__panel {
    position: absolute;
    left: 0; right: 0; top: 204px; bottom: 0;
    background: var(--navy);
  }
  .holder {
    position: absolute;
    left: 0; right: 0; top: 163px;
    text-align: center;
    color: var(--ink-dark);
  }
  .holder__name { font-weight: 700; font-size: 20px; letter-spacing: 1px; }
  .holder__company { font-size: 12px; margin-left: 4px; }
  .contact {
    position: absolute;
    left: 0; right: 0; top: 218px;
    font-size: 12.5px;
    color: var(--white);
    text-align: center;
    line-height: 22px;
  }
  .contact__row { display: flex; justify-content: center; align-items: center; gap: 6px; }
  .contact__gap { width: 12px; }
  .contact__email { letter-spacing: 1px; }
  .icon { width: 11px; height: 11px; fill: var(--white); }

  /* back */
  .back__web {
    position: absolute;
    left: 0; right: 0; top: 238px;
    text-align: center;
    font-weight: 700;
    font-size: 12px;
    color: var(--white);
    letter-spacing: 7px;
  }
</style>
</head>
<body>
  <section class="card card--front" aria-label="Business card, front">
    <div class="brand front__brand"><span class="brand__mark"></span><span>Velmora Partners</span></div>
    <div class="front__band"></div>
    <div class="front__rule"></div>
    <div class="front__panel"></div>
    <p class="holder">
      <span class="holder__name">Luis R. Abadal,</span>
      <span class="holder__company">Velmora Partners S.L.</span>
    </p>
    <div class="contact">
      <div class="contact__row">
        <svg class="icon" viewBox="0 0 12 12" aria-hidden="true"><path d="M2.5 0.8 4.3 3.2 3.3 4.4c.6 1.6 1.9 2.9 3.4 3.5l1.1-1 2.4 1.7-.9 2.2C5.6 10.7 1.4 6.6.4 1.8z"/></svg>
        <span>+34 (91) 387-2265</span>
        <span class="contact__gap"></span>
        <svg class="icon" viewBox="0 0 12 12" aria-hidden="true"><path d="M3.5 0h5a1 1 0 0 1 1 1v10a1 1 0 0 1-1 1h-5a1 1 0 0 1-1-1V1a1 1 0 0 1 1-1zm.5 1.5v7h4v-7z"/></svg>
        <span>+34 (646) 819-054</span>
      </div>
      <div class="contact__row">
        <svg class="icon" viewBox="0 0 12 12" aria-hidden="true"><path d="M0 2.5h12v7H0zm1 1v.3l5 3 5-3v-.3z"/></svg>
        <span class="contact__email">labadal@velmorapartners.com</span>
      </div>
      <div class="contact__row">
        <span>Casa de Torrelumbre, Calle de Vientoalto 27, 28014 Madrid</span>
      </div>
    </div>
  </section>

  <section class="card card--back" aria-label="Business card, back">
    <div class="brand back__brand"><span class="brand__mark"></span><span>Velmora Partners</span></div>
    <div class="back__web">www.velmora.com</div>
  </section>
</body>
</html>
```